VOMRA Pty Ltd Business Card

Looking for a simple yet eye-catching double-sided business card design using my company logo on one side and contact details on the other.

Target Market(s)

Government

Industry/Entity Type

Communication Systems Engineering

Contact Information for Business Card

VOMRA Pty Ltd

Requirements
Nice to have
• Would be great to have a QR code so details can be scanned into contacts

```html
<!DOCTYPE html>
<html lang="en">
<head>
<meta charset="utf-8">
<title>VOMRA Pty Ltd Business Card</title>
<link rel="stylesheet" href="https://fonts.googleapis.com/css2?family=Open+Sans:wght@400;700&display=swap">
<style>
  :root {
    --backdrop: #222222;
    --card: #ffffff;
    --ink: #333d44;
    --text: #1f2326;
  }
  * { box-sizing: border-box; margin: 0; padding: 0; }
  html, body { width: 1200px; height: 780px; overflow: hidden; }
  body {
    background: var(--backdrop);
    font-family: "Open Sans", Arial, sans-serif;
    display: flex;
    align-items: center;
    justify-content: center;
    gap: 80px;
  }
  .card {
    width: 340px;
    height: 580px;
    background: var(--card);
    position: relative;
    overflow: hidden;
  }
  .card--back { border-radius: 140px 140px 0 0; }
  .card--front { border-radius: 0 0 140px 140px; }

  /* back side */
  .back-wordmark {
    position: absolute;
    left: 50%;
    top: 56px;
    transform: translateX(-50%);
    writing-mode: vertical-rl;
    font-weight: 700;
    font-size: 72px;
    line-height: 1;
    letter-spacing: 4px;
    color: var(--ink);
    white-space: nowrap;
  }
  .back-mark {
    position: absolute;
    left: 50%;
    bottom: 90px;
    width: 100px;
    height: 100px;
    margin-left: -50px;
    border-radius: 50%;
    background: var(--ink);
  }

  /* front side */
  .front-logo {
    position: absolute;
    top: 56px;
    left: 0;
    right: 0;
    display: flex;
    align-items: center;
    justify-content: center;
    gap: 16px;
  }
  .front-logo__mark {
    width: 58px;
    height: 58px;
    border-radius: 50%;
    background: var(--ink);
  }
  .front-logo__name {
    font-weight: 700;
    font-size: 46px;
    letter-spacing: 3px;
    color: var(--ink);
  }
  .contact {
    position: absolute;
    top: 290px;
    left: 0;
    right: 0;
    text-align: center;
    color: var(--text);
  }
  .contact__name { font-weight: 700; font-size: 24px; color: var(--ink); line-height: 1.1; }
  .contact__role { font-size: 14px; margin-bottom: 10px; }
  .contact__icons { display: flex; justify-content: center; gap: 6px; margin-bottom: 6px; }
  .contact__icons svg, .contact__pin { width: 22px; height: 22px; display: block; }
  .contact__line { font-size: 14px; line-height: 1.3; }
  .contact__pin { margin: 12px auto 10px; }
  .contact__address { font-size: 14px; line-height: 1.3; }
</style>
</head>
<body>
  <div class="card card--back">
    <div class="back-wordmark">VOMRA</div>
    <div class="back-mark"></div>
  </div>

  <div class="card card--front">
    <div class="front-logo">
      <span class="front-logo__mark"></span>
      <span class="front-logo__name">VOMRA</span>
    </div>

    <div class="contact">
      <p class="contact__name">Daniel Hartley</p>
      <p class="contact__role">Co-Founder</p>
      <div class="contact__icons">
        <svg viewBox="0 0 22 22" aria-label="Phone"><circle cx="11" cy="11" r="11" fill="#333d44"/><path d="M7.5 6.5l2 .2.6 2.2-1.2.9a7 7 0 003.3 3.3l.9-1.2 2.2.6.2 2-1.3 1A9 9 0 016.5 7.8z" fill="#fff"/></svg>
        <svg viewBox="0 0 22 22" aria-label="Email"><circle cx="11" cy="11" r="11" fill="#333d44"/><rect x="6" y="7.5" width="10" height="7" fill="none" stroke="#fff" stroke-width="1.2"/><path d="M6 7.5l5 4 5-4" fill="none" stroke="#fff" stroke-width="1.2"/></svg>
        <svg viewBox="0 0 22 22" aria-label="Website"><circle cx="11" cy="11" r="11" fill="#333d44"/><circle cx="11" cy="11" r="5.5" fill="none" stroke="#fff" stroke-width="1.2"/><ellipse cx="11" cy="11" rx="2.3" ry="5.5" fill="none" stroke="#fff" stroke-width="1"/><path d="M5.5 11h11" stroke="#fff" stroke-width="1"/></svg>
      </div>
      <p class="contact__line">(555) 204-7731</p>
      <p class="contact__line">www.vomra.com.au</p>
      <p class="contact__line">admin@vomra.com.au</p>
      <svg class="contact__pin" viewBox="0 0 22 22" aria-label="Address"><circle cx="11" cy="11" r="11" fill="#333d44"/><path d="M11 5a4 4 0 00-4 4c0 3 4 7.5 4 7.5s4-4.5 4-7.5a4 4 0 00-4-4z" fill="#fff"/><circle cx="11" cy="9" r="1.5" fill="#333d44"/></svg>
      <p class="contact__address">27-29 Wattle Road Kellyville<br>NSW 2155 Australia</p>
    </div>
  </div>
</body>
</html>
```